VORTAL MED -DIAGNOSTIC CENTRE FOR IMAGES

Our Activity provides diagnostic services for images (RMI, Tac, RX, Ultrasound etc.)
We would like to create a broschure that illustrates our services.
We would like to give maximum attention to the Diagnostic service dedicated to "HEART", therefore maximum evidence to the world of Cardiology.
In the background we would like to highlight the other diagnostic services dedicated to the Rest of the Body (Brain, Knees Legs etc.)
Target Market(s)
PERSONS WHO NEED TO PERFORM DIAGNOSTIC TESTS (MRI, CT, ULTRASOUND, RX ETC.)
Industry/Entity Type
HEALTH
Requirements
Must have
- The company logo, must have diagnostic images (MRI, CT, X-ray, ultrasound), must be simple and intuitive, which is harmonious with the colors of our company logo
Should not have
- Colours that are not in harmony with our company logo

```html
<!DOCTYPE html>
<html lang="en">
<head>
<meta charset="utf-8">
<title>Vortal Med – Diagnostic Brochure</title>
<link href="https://fonts.googleapis.com/css2?family=Barlow:wght@400;500;600;700&family=Inter:wght@400;500;600;700&display=swap" rel="stylesheet">
<style>
  :root{
    --teal:#3bb0a4;
    --teal-dark:#249a8d;
    --navy:#2d4a68;
    --steel:#3f78ad;
    --ink:#3a3d42;
    --muted:#5d636b;
    --paper:#f4f5f6;
    --paper-shade:#e9ebed;
    --deco:#dbe8ef;
    --panel:#2f3133;
    --canvas:#e3e6e9;
  }
  *{box-sizing:border-box;margin:0;padding:0}
  html,body{width:1200px;height:900px;overflow:hidden}
  body{background:var(--canvas);font-family:"Inter",Arial,sans-serif;color:var(--ink);position:relative}
  .spread{position:absolute;left:300px;width:600px;height:428px;display:flex;box-shadow:0 6px 18px rgba(40,50,60,.18)}
  .spread--outside{top:16px}
  .spread--inside{top:456px}
  .page{position:relative;width:300px;height:428px;background:var(--paper);overflow:hidden}
  .page--left{background:linear-gradient(90deg,var(--paper) 0%,var(--paper) 88%,var(--paper-shade) 100%)}
  .page--right{background:linear-gradient(90deg,#fafbfb 0%,var(--paper) 10%)}
  .abs{position:absolute}

  /* decoration */
  .bar{position:absolute;height:5px;border-radius:3px}
  .bar--teal{background:var(--teal)}
  .bar--navy{background:var(--navy)}
  .notch{position:absolute;border:1.2px solid var(--navy);border-top:none;border-radius:0 0 6px 6px;height:18px;width:52px}
  .notch--up{border-top:1.2px solid var(--navy);border-bottom:none;border-radius:6px 6px 0 0}
  .ring{position:absolute;width:14px;height:14px;border:1.6px solid var(--teal);border-radius:50%}
  .plus{position:absolute;opacity:.9}
  .plus::before,.plus::after{content:"";position:absolute;background:var(--deco);border-radius:3px}
  .plus::before{left:33%;top:0;width:34%;height:100%}
  .plus::after{top:33%;left:0;height:34%;width:100%}
  .soft-block{position:absolute;background:var(--deco);border-radius:8px;opacity:.8}
  .outline-block{position:absolute;border:1.2px solid var(--navy);border-right:none;border-radius:8px 0 0 8px}
  .dots{position:absolute;display:grid;grid-template-columns:repeat(4,3px);gap:7px}
  .dots i{width:3px;height:3px;background:var(--navy);border-radius:50%;display:block}
  .tri-stack{position:absolute;display:flex;flex-direction:column;gap:3px}
  .tri-stack i{width:0;height:0;border-left:5px solid transparent;border-right:5px solid transparent;border-bottom:7px solid var(--teal);display:block}

  /* brand name */
  .brand{position:absolute;display:flex;align-items:center;gap:5px;font-family:"Barlow",Arial,sans-serif;font-weight:700;color:var(--teal-dark);letter-spacing:.5px;white-space:nowrap}
  .brand i{display:block;border-radius:50%;background:var(--teal-dark)}

  /* cover */
  .cover-title{position:absolute;left:0;width:100%;text-align:center;font-family:"Barlow",Arial,sans-serif;color:var(--teal)}
  .cover-title .lead{display:block;font-size:20px;font-weight:500;color:var(--steel);letter-spacing:.5px;line-height:1}
  .cover-title .main{display:block;font-size:28px;font-weight:700;color:var(--teal-dark);letter-spacing:.5px;line-height:1.05}
  .cover-title .sub{display:block;margin-top:4px;font-family:"Inter",Arial,sans-serif;font-size:8px;color:var(--muted)}
  .portrait{position:absolute;border-radius:50%;background:radial-gradient(circle at 50% 40%,#e9eef0 0 34%,var(--teal) 35%,var(--teal-dark) 100%)}
  .pill{position:absolute;font-size:6.4px;color:#fff;background:var(--steel);padding:2px 6px;border-radius:2px;white-space:nowrap;line-height:1.3}
  .tag{display:inline-block;font-size:6.2px;color:#fff;background:var(--teal);padding:2px 5px;border-radius:2px;white-space:nowrap;line-height:1.3}

  /* back page */
  .photo{position:absolute;border-radius:9px;overflow:hidden}
  .photo--mri{background:linear-gradient(160deg,#d5dbe1 0%,#eef0f2 45%,#c8d2db 70%,#9cc6e0 100%)}
  .photo .brand{left:50%;top:50%;transform:translate(-50%,-50%)}
  .service{position:absolute;width:70px;text-align:center;font-size:6.6px;font-weight:700;color:var(--ink);line-height:1.2}
  .service .tile{width:32px;height:32px;margin:0 auto 4px;background:var(--teal);border-radius:4px;display:flex;align-items:center;justify-content:center}
  .contact-head{position:absolute;font-family:"Barlow",Arial,sans-serif;font-weight:700;font-size:10.5px;line-height:1.35}
  .contact-head span{display:block}
  .contact-head .a{color:var(--navy)}
  .contact-head .b{color:var(--teal)}
  .contact-lines{position:absolute;font-size:6.8px;color:var(--ink);line-height:1.45}

  /* inside */
  .section-head{position:absolute;font-family:"Barlow",Arial,sans-serif;font-weight:600;font-size:14px;line-height:1.15;letter-spacing:.3px}
  .section-head .a{display:block;color:var(--navy)}
  .section-head .b{display:block;color:var(--teal)}
  .intro{position:absolute;font-size:6.3px;line-height:1.5;color:var(--ink)}
  .equipment{position:absolute;border-radius:4px;background:linear-gradient(180deg,#e2e4e7 0%,#cfd4d9 45%,#e7e9eb 55%,#d4d8dc 100%)}
  .service-list{position:absolute;left:116px;top:118px;width:170px}
  .service-item{margin-bottom:6px}
  .service-item h3{display:inline-block;font-size:7.2px;font-weight:600;color:#fff;background:var(--teal);padding:1px 4px;border-radius:1px;margin-bottom:1px}
  .service-item p{font-size:5.9px;line-height:1.42;color:var(--ink);text-align:justify}
  .benefits h4{font-size:7.6px;font-weight:600;color:var(--navy);margin-bottom:3px}
  .benefits .tags{display:flex;flex-wrap:wrap;gap:4px}
  .scanner{position:absolute;border-radius:6px;background:radial-gradient(circle at 40% 45%,#dfe6ea 0 16%,#f6f7f8 17% 40%,#e3e7ea 60%,var(--paper) 75%)}
  .tag-cloud{position:absolute;left:152px;top:130px;width:140px;display:flex;flex-direction:column;gap:6px;align-items:flex-start}
  .tag-cloud .row{display:flex;gap:5px}
  .check-panel{position:absolute;left:12px;top:260px;width:250px;height:126px;background:var(--panel);border-radius:8px;padding:13px 10px 0 12px;display:grid;grid-template-columns:1fr 1fr;column-gap:8px;row-gap:9px;align-content:start}
  .check{display:flex;gap:5px;font-size:6.1px;line-height:1.35;color:#f1f2f3}
  .check svg{flex:none;margin-top:1px}
</style>
</head>
<body>

<!-- OUTSIDE: back cover + front cover -->
<section class="spread spread--outside" aria-label="Brochure outside">
  <article class="page page--left" aria-label="Back cover">
    <div class="notch" style="left:36px;top:0"></div>
    <div class="ring" style="left:232px;top:22px"></div>
    <div class="soft-block" style="left:0;top:40px;width:40px;height:40px;opacity:.5"></div>
    <div class="bar bar--teal" style="left:18px;top:38px;width:100px"></div>
    <div class="photo photo--mri" style="left:26px;top:54px;width:248px;height:168px" role="img" aria-label="MRI scanner in a bright examination room">
      <div class="brand" style="font-size:22px;color:var(--teal)"><i style="width:10px;height:10px;background:var(--teal)"></i>VORTAL MED</div>
    </div>

    <div class="service" style="left:39px;top:206px">
      <div class="tile"><svg width="16" height="16" viewBox="0 0 24 24" fill="none" stroke="#fff" stroke-width="1.8" stroke-linecap="round" stroke-linejoin="round"><path d="M12 20s-7-4.4-7-10a4 4 0 0 1 7-2.6A4 4 0 0 1 19 10c0 5.6-7 10-7 10z"/><path d="M5 12h4l1.5-2 2 4 1.5-2H19"/></svg></div>Cardiology<br>Services</div>
    <div class="service" style="left:115px;top:206px">
      <div class="tile"><svg width="16" height="16" viewBox="0 0 24 24" fill="none" stroke="#fff" stroke-width="1.8" stroke-linecap="round"><path d="M9 4a3 3 0 0 0-3 3 3 3 0 0 0-2 5 3 3 0 0 0 2 5 3 3 0 0 0 6 1V6a2 2 0 0 0-3-2z"/><path d="M15 4a3 3 0 0 1 3 3 3 3 0 0 1 2 5 3 3 0 0 1-2 5 3 3 0 0 1-6 1"/></svg></div>Neurology<br>Scans</div>
    <div class="service" style="left:191px;top:206px">
      <div class="tile"><svg width="16" height="16" viewBox="0 0 24 24" fill="none" stroke="#fff" stroke-width="1.8" stroke-linecap="round"><rect x="5" y="3" width="14" height="18" rx="2"/><circle cx="12" cy="8" r="1.6"/><path d="M12 10v6M9 12h6M10 19l2-3 2 3"/></svg></div>Full-body<br>Scans</div>
    <div class="service" style="left:77px;top:270px">
      <div class="tile"><svg width="16" height="16" viewBox="0 0 24 24" fill="none" stroke="#fff" stroke-width="1.8" stroke-linecap="round"><rect x="5" y="3" width="14" height="18" rx="2"/><path d="M10 7h4v4h-4zM12 11v3M10 17l2-3 2 3"/></svg></div>Orthopedic<br>Scans</div>
    <div class="service" style="left:153px;top:270px">
      <div class="tile"><svg width="16" height="16" viewBox="0 0 24 24" fill="none" stroke="#fff" stroke-width="1.8" stroke-linecap="round"><circle cx="12" cy="7" r="3"/><path d="M5 19c1-4 4-6 7-6s6 2 7 6"/><path d="M8 16h3l1-2 1.5 3 1-1H17"/></svg></div>Customized<br>Care</div>

    <div class="plus" style="left:14px;top:282px;width:34px;height:34px"></div>
    <div class="dots" style="left:246px;top:282px"><i></i><i></i><i></i><i></i><i></i><i></i><i></i><i></i><i></i><i></i><i></i><i></i><i></i><i></i><i></i><i></i></div>

    <div class="contact-head" style="left:18px;top:338px"><span class="a">FOR APPOINTMENTS AND INQUIRIES</span><span class="b">CONTACT US TODAY!</span></div>
    <div class="contact-lines" style="left:22px;top:370px">Addressline 1<br>Addressline 2</div>
    <div class="contact-lines" style="left:22px;top:402px">Phone no: +12 3456 789</div>
    <div class="soft-block" style="left:240px;top:370px;width:60px;height:58px;opacity:.55"></div>
    <div class="brand" style="left:198px;top:396px;font-size:11px"><i style="width:6px;height:6px"></i>VORTAL MED</div>
    <div class="notch notch--up" style="left:122px;top:410px"></div>
  </article>

  <article class="page page--right" aria-label="Front cover">
    <div class="plus" style="left:26px;top:0;width:64px;height:64px"></div>
    <div class="bar bar--navy" style="left:196px;top:18px;width:104px;height:4px"></div>
    <div class="soft-block" style="left:270px;top:48px;width:40px;height:110px"></div>
    <div class="outline-block" style="left:275px;top:122px;width:30px;height:52px"></div>
    <div class="brand" style="left:50%;top:42px;transform:translateX(-50%);font-size:17px"><i style="width:8px;height:8px"></i>VORTAL MED</div>
    <div class="cover-title" style="top:84px">
      <span class="lead">YOUR HEART</span>
      <span class="main">MATTERS</span>
      <span class="sub">Diagnostic Services for a Healthier You</span>
    </div>
    <div class="tri-stack" style="left:20px;top:132px"><i></i><i></i><i></i><i></i></div>
    <div class="portrait" style="left:72px;top:198px;width:150px;height:150px" role="img" aria-label="Smiling doctor in a white coat holding a red heart"></div>
    <div class="abs" style="left:252px;top:212px;width:34px;height:34px;background:var(--teal-dark);border-radius:4px"></div>
    <div class="ring" style="left:-7px;top:328px"></div>
    <div class="pill" style="left:38px;top:364px">Highly Experienced Staff</div>
    <div class="pill" style="left:162px;top:364px">Knowledgeable Support Staff</div>
    <div class="pill" style="left:44px;top:386px">Friendly Environment</div>
    <div class="pill" style="left:172px;top:386px">Cutting-edge Systems</div>
    <div class="soft-block" style="left:0;top:385px;width:50px;height:43px;opacity:.5"></div>
    <div class="bar bar--teal" style="left:10px;top:412px;width:104px;height:3px"></div>
  </article>
</section>

<!-- INSIDE: cardiology focus + other diagnostics -->
<section class="spread spread--inside" aria-label="Brochure inside">
  <article class="page page--left" aria-label="Cardiology page">
    <div class="soft-block" style="left:0;top:0;width:30px;height:20px"></div>
    <div class="notch" style="left:12px;top:0;width:40px;height:10px"></div>
    <div class="section-head" style="left:18px;top:24px"><span class="a">OUR MAIN FOCUS</span><span class="b">CARDIOLOGY EXCELLENCE</span></div>
    <svg class="abs" style="left:262px;top:24px" width="12" height="12" viewBox="0 0 12 12"><path d="M6 0v4M6 8v4M0 6h4M8 6h4" stroke="#2d4a68" stroke-width="1"/></svg>
    <p class="intro" style="left:18px;top:62px;width:270px">At Vortal Med, we are dedicated to delivering exceptional cardiac care to safeguard your heart health. Our cutting-edge technology and skilled medical professionals are committed to providing you with accurate diagnoses and effective treatments, ensuring your heart remains in the best possible condition.</p>

    <div class="equipment" style="left:16px;top:120px;width:96px;height:118px" role="img" aria-label="Cardiac ultrasound machine with monitor"></div>
    <div class="equipment" style="left:16px;top:248px;width:96px;height:118px" role="img" aria-label="Digital X-ray system with table and detector"></div>

    <div class="service-list">
      <div class="service-item"><h3>Cardiac Imaging</h3><p>We offer advanced cardiac imaging services, including state-of-the-art MRI and CT scans, to provide a comprehensive view of your heart's structure and function</p></div>
      <div class="service-item"><h3>Electrocardiography (ECG/EKG)</h3><p>Our ECG/EKG tests accurately monitor your heart's electrical activity, helping to diagnose arrhythmias, heart attacks, and other cardiac conditions.</p></div>
      <div class="service-item"><h3>Echocardiography</h3><p>Our high-resolution echocardiography allows us to assess your heart's chambers, valves, and blood flow, aiding in the detection of heart diseases.</p></div>
      <div class="service-item"><h3>Holter Monitoring</h3><p>For continuous heart monitoring, our Holter monitors record your heart's activity over 24 hours or more, helping us identify irregularities that may go unnoticed in shorter tests.</p></div>
      <div class="benefits"><h4>Other Benefits</h4>
        <div class="tags"><span class="tag">Stress Testing</span><span class="tag">Coronary Angiography</span><span class="tag">Cardiac Consultations</span></div>
      </div>
    </div>
    <div class="bar bar--navy" style="left:0;top:414px;width:100px;height:5px"></div>
  </article>

  <article class="page page--right" aria-label="Comprehensive diagnostics page">
    <div class="plus" style="left:40px;top:0;width:50px;height:50px"></div>
    <div class="bar bar--navy" style="left:196px;top:12px;width:96px;height:4px"></div>
    <div class="section-head" style="left:14px;top:24px"><span class="a">COMPREHENSIVE DIAGNOSTICS</span><span class="b">BEYOND CARDIOLOGY</span></div>
    <div class="abs" style="left:264px;top:46px;width:12px;height:12px;background:var(--teal);border-radius:2px"></div>
    <div class="dots" style="left:266px;top:26px;grid-template-columns:repeat(3,2px);gap:4px"><i></i><i></i><i></i><i></i><i></i><i></i><i></i><i></i><i></i></div>
    <p class="intro" style="left:14px;top:62px;width:272px">In addition to our specialized cardiology services, we offer a wide range of comprehensive diagnostic services to address your healthcare needs holistically. At [Your Company Name], we believe in the importance of thorough diagnostics to ensure your overall well-being. Our diagnostic services include:</p>

    <div class="scanner" style="left:12px;top:126px;width:134px;height:100px" role="img" aria-label="CT scanner with patient table"></div>
    <div class="tag-cloud">
      <div class="row"><span class="tag">Neuroimaging</span><span class="tag">Ultrasound</span></div>
      <span class="tag">Musculoskeletal Imaging</span>
      <span class="tag">Abdominal Imaging</span>
      <span class="tag">Multi-Specialty Consultations</span>
      <span class="tag">X-rays (RX)</span>
    </div>

    <div class="check-panel">
      <div class="check"><svg width="7" height="7" viewBox="0 0 10 10"><path d="M1 5l3 3 5-6" fill="none" stroke="#3bb0a4" stroke-width="1.8"/></svg><span>Enhanced treatment planning for cardiac conditions.</span></div>
      <div class="check"><svg width="7" height="7" viewBox="0 0 10 10"><path d="M1 5l3 3 5-6" fill="none" stroke="#3bb0a4" stroke-width="1.8"/></svg><span>Cutting-edge technology for precise imaging.</span></div>
      <div class="check"><svg width="7" height="7" viewBox="0 0 10 10"><path d="M1 5l3 3 5-6" fill="none" stroke="#3bb0a4" stroke-width="1.8"/></svg><span>Personalized care for better patient outcomes.</span></div>
      <div class="check"><svg width="7" height="7" viewBox="0 0 10 10"><path d="M1 5l3 3 5-6" fill="none" stroke="#3bb0a4" stroke-width="1.8"/></svg><span>Comprehensive fusion of PET and CT scans.</span></div>
      <div class="check"><svg width="7" height="7" viewBox="0 0 10 10"><path d="M1 5l3 3 5-6" fill="none" stroke="#3bb0a4" stroke-width="1.8"/></svg><span>Enhanced treatment planning for cardiac conditions.</span></div>
      <div class="check"><svg width="7" height="7" viewBox="0 0 10 10"><path d="M1 5l3 3 5-6" fill="none" stroke="#3bb0a4" stroke-width="1.8"/></svg><span>Minimized radiation exposure with optimized protocols.</span></div>
      <div class="check"><svg width="7" height="7" viewBox="0 0 10 10"><path d="M1 5l3 3 5-6" fill="none" stroke="#3bb0a4" stroke-width="1.8"/></svg><span>Enhanced detection and localization of cardiac issues.</span></div>
      <div class="check"><svg width="7" height="7" viewBox="0 0 10 10"><path d="M1 5l3 3 5-6" fill="none" stroke="#3bb0a4" stroke-width="1.8"/></svg><span>Experienced nuclear medicine specialists.</span></div>
    </div>
    <div class="tri-stack" style="left:270px;top:330px"><i></i><i></i><i></i><i></i></div>
    <div class="soft-block" style="left:236px;top:362px;width:30px;height:26px"></div>
    <div class="notch notch--up" style="left:204px;top:410px"></div>
  </article>
</section>

</body>
</html>
```